Harborline Claims Advocates Business card

We need to get business card Design for our Company we are Public Adjusters in Chicago Illinois - i like to see good combination and elements from my Company Logo. as well To be an two side design
Updates

Target Market(s)

Home /Business owner Property Managers

Industry/Entity Type

Business

Contact Information for Business Card

to show the Element of our logo i will Like 3D

Font styles to use
Sans Serif

Requirements
Must have
• Logo and Element of the Logo in 3D
Nice to have
• Logo That we Provide 3D Same Colors or open for suggestions
Should not have
• unleare view -

```html
<!DOCTYPE html>
<html lang="en">
<head>
<meta charset="utf-8">
<title>Harborline Claims Advocates – Business Card</title>
<link rel="stylesheet" href="https://fonts.googleapis.com/css2?family=Open+Sans:wght@400;600;700&display=swap">
<style>
  :root {
    --page-bg: #e6e6e6;
    --card-white: #ffffff;
    --brand-blue: #1c2fb8;
    --accent-red: #c8372d;
    --text-gray: #555b63;
    --rule-gray: #d4d4d4;
    --navy-edge: #13103f;
    --navy-mid: #1530a8;
    --navy-glow: #1f4fe0;
  }
  * { box-sizing: border-box; margin: 0; padding: 0; }
  html, body {
    width: 1200px; height: 987px; overflow: hidden;
    background: var(--page-bg);
    font-family: "Open Sans", Arial, sans-serif;
  }
  .canvas { position: relative; width: 1200px; height: 987px; }

  .card {
    position: absolute; left: 293px; width: 615px; height: 351px;
    box-shadow: 0 2px 4px rgba(0,0,0,0.18);
  }
  .card-front { top: 130px; background: var(--card-white); }
  .card-back {
    top: 505px;
    background: radial-gradient(ellipse 60% 80% at 50% 45%, var(--navy-glow) 0%, var(--navy-mid) 45%, var(--navy-edge) 100%);
  }

  /* Front */
  .brand-block {
    position: absolute; left: 15px; top: 72px; width: 300px;
    display: flex; flex-direction: column; align-items: center; gap: 44px;
    text-align: center;
  }
  .brand-dot {
    width: 116px; height: 116px; border-radius: 50%;
    background: var(--brand-blue);
  }
  .brand-name {
    color: var(--brand-blue); font-weight: 700; font-size: 16px; line-height: 1.2;
    white-space: nowrap;
  }
  .divider {
    position: absolute; left: 320px; top: 58px; width: 1px; height: 232px;
    background: var(--rule-gray);
  }
  .contact-block { position: absolute; left: 355px; top: 60px; }
  .person-name {
    color: var(--brand-blue); font-weight: 600; font-size: 22px; line-height: 1.1;
    letter-spacing: 0.3px;
  }
  .person-title { color: var(--accent-red); font-size: 16px; margin-top: 4px; }
  .address { color: var(--text-gray); font-size: 15px; line-height: 23px; margin-top: 12px; }
  .contact-list { list-style: none; margin-top: 9px; }
  .contact-list li {
    display: flex; align-items: center; gap: 8px;
    color: var(--text-gray); font-size: 15px; line-height: 23.5px;
  }
  .contact-list svg { width: 14px; height: 14px; fill: var(--brand-blue); flex: none; }

  /* Back */
  .back-brand {
    position: absolute; left: 0; top: 92px; width: 100%;
    display: flex; flex-direction: column; align-items: center; gap: 14px;
  }
  .back-dot { width: 124px; height: 124px; border-radius: 50%; background: var(--card-white); }
  .back-name { color: var(--card-white); font-weight: 700; font-size: 19px; line-height: 1.2; }
  .back-rule {
    position: absolute; left: 85px; top: 272px; width: 445px; height: 1px;
    background: linear-gradient(90deg, transparent, rgba(255,255,255,0.45), transparent);
  }
  .back-url {
    position: absolute; left: 0; top: 284px; width: 100%;
    text-align: center; color: var(--card-white); font-size: 16px; letter-spacing: 2.2px;
  }
</style>
</head>
<body>
<main class="canvas">
  <section class="card card-front">
    <div class="brand-block">
      <div class="brand-dot"></div>
      <div class="brand-name">Harborline Claims Advocates, Inc.</div>
    </div>
    <div class="divider"></div>
    <div class="contact-block">
      <div class="person-name">DANIEL REYES</div>
      <div class="person-title">CEO/Founder</div>
      <div class="address">2140 Larkspur Avenue<br>Chicago, Illinois 60614</div>
      <ul class="contact-list">
        <li><svg viewBox="0 0 16 16"><path d="M3.6 1.2l2.3 2.6-1.3 1.8c.9 2 2.5 3.6 4.5 4.5l1.8-1.3 2.6 2.3-1.3 2.7C7 13.5 2.5 9 1 3.1z"/></svg>312 555 0148</li>
        <li><svg viewBox="0 0 16 16"><path d="M4.5 0h7A1.5 1.5 0 0 1 13 1.5v13a1.5 1.5 0 0 1-1.5 1.5h-7A1.5 1.5 0 0 1 3 14.5v-13A1.5 1.5 0 0 1 4.5 0zM5 2v10h6V2zm3 11a1 1 0 1 0 0 2 1 1 0 0 0 0-2z"/></svg>312 555 0193</li>
        <li><svg viewBox="0 0 16 16"><path d="M4 1h8v4H4zM1 6h14v7h-2v2H3v-2H1zm4 5v2h6v-2z"/></svg>312 555 0176</li>
        <li><svg viewBox="0 0 16 16"><path d="M1 3h14v10H1zm1.5 1.5v.3L8 9l5.5-4.2v-.3zm0 2.2v4.8h11V6.7L8 10.9z"/></svg>info@harborlineclaims.com</li>
        <li><svg viewBox="0 0 16 16"><path d="M8 1a7 7 0 1 0 0 14A7 7 0 0 0 8 1zm-1 2.2c-.8.9-1.5 2-1.2 2.8.4.9 1.8.6 2.2 1.6.4 1-1 1.8-.4 3 .4.8 1.4 1.2 1.4 2.3A5 5 0 0 1 7 3.2zm3 .4a5 5 0 0 1 2.7 5.6c-.8-.6-1.6-.4-2-1.3-.5-1 .6-1.7.1-2.7-.3-.6-.9-.9-.8-1.6z"/></svg>www.harborlineclaims.com</li>
      </ul>
    </div>
  </section>

  <section class="card card-back">
    <div class="back-brand">
      <div class="back-dot"></div>
      <div class="back-name">Harborline Claims Advocates</div>
    </div>
    <div class="back-rule"></div>
    <div class="back-url">www.HarborlineClaimsAdvocates.com</div>
  </section>
</main>
</body>
</html>
```